business card - Helicopter Flight Services, Flight School, etc.

We need a business card design for a new helicopter service.

We offer Helicopter Flight Services, Aerial Filming & Photography, Flight School, and Helicopter Tours. In that order.

Summit BladeAir, Inc.
Dennis Tollerby
SummitBladeair@Kestmail.com
626-418-7352

Based at the Brenwick Airport in Van Nuys, CA. The final design should communicate integrity and safety. Pictures or logos at your discretion.

Card back side - surprise me.

```html
<!DOCTYPE html>
<html lang="en">
<head>
<meta charset="utf-8">
<title>Summit BladeAir, Inc. — Business Card</title>
<link rel="stylesheet" href="https://fonts.googleapis.com/css2?family=Bodoni+Moda:wght@500;600&family=Arimo:wght@400&display=swap">
<style>
  :root {
    --page-bg: #e9e7e3;
    --card-white: #fbfbfa;
    --ink: #1c1c1c;
    --ink-soft: #333333;
    --rule: #2a2a2a;
    --sky-top: #5a6ea8;
    --sky-pink: #c98fb0;
    --sky-glow: #e9b7c2;
    --pad-blue: #2f3475;
    --pad-deep: #1f2458;
    --band: rgba(255, 255, 255, 0.72);
    --shadow: rgba(0, 0, 0, 0.18);
  }
  * { margin: 0; padding: 0; box-sizing: border-box; }
  html, body {
    width: 1200px; height: 892px; overflow: hidden;
    background: var(--page-bg);
  }
  .canvas {
    position: relative; width: 1200px; height: 892px;
  }
  .card {
    position: absolute; left: 290px;
    width: 620px; height: 354px;
    box-shadow: 0 6px 18px var(--shadow);
    overflow: hidden;
  }
  /* front side */
  .card-front { top: 70px; background: var(--card-white); }
  .front-company {
    position: absolute; right: 40px; top: 34px;
    font-family: "Bodoni Moda", serif; font-weight: 600;
    font-size: 31px; letter-spacing: 0.5px; color: var(--ink);
    text-transform: uppercase;
  }
  .front-rule {
    position: absolute; left: 40px; right: 40px; top: 88px;
    height: 1px; background: var(--rule);
  }
  .front-name {
    position: absolute; left: 0; right: 0; top: 150px;
    text-align: center;
    font-family: "Bodoni Moda", serif; font-weight: 500;
    font-size: 26px; color: var(--ink-soft);
  }
  .front-contact {
    position: absolute; left: 0; right: 0; top: 220px;
    text-align: center;
    font-family: "Arimo", sans-serif; font-size: 17px;
    line-height: 27px; color: var(--ink);
  }
  /* back side */
  .card-back { top: 468px; }
  .back-photo { position: absolute; inset: 0; width: 100%; height: 100%; }
  .back-band {
    position: absolute; left: 0; right: 0; top: 142px; height: 104px;
    background: var(--band);
    text-align: center; padding-top: 12px;
  }
  .back-company {
    font-family: "Bodoni Moda", serif; font-weight: 600;
    font-size: 36px; letter-spacing: 1px; color: var(--ink);
    text-transform: uppercase; line-height: 46px;
  }
  .back-services {
    font-family: "Bodoni Moda", serif; font-weight: 600;
    font-size: 22px; color: var(--ink-soft); line-height: 34px;
  }
</style>
</head>
<body>
<div class="canvas">
  <section class="card card-front">
    <h1 class="front-company">Summit BladeAir, Inc.</h1>
    <div class="front-rule"></div>
    <p class="front-name">Dennis Tollerby</p>
    <p class="front-contact">
      626-418-7352<br>
      SummitBladeair@Kestmail.com<br>
      2740 W. Larkin Ave. Ste.B &nbsp;Brenwick, CA 91408
    </p>
  </section>

  <section class="card card-back">
    <svg class="back-photo" viewBox="0 0 620 354" preserveAspectRatio="none" role="img" aria-label="Photograph of a helicopter parked on a helipad at sunset">
      <defs>
        <linearGradient id="sunset-scene" x1="0" y1="0" x2="0" y2="1">
          <stop offset="0" stop-color="var(--sky-top)"/>
          <stop offset="0.28" stop-color="var(--sky-pink)"/>
          <stop offset="0.42" stop-color="var(--sky-glow)"/>
          <stop offset="0.6" stop-color="var(--pad-blue)"/>
          <stop offset="1" stop-color="var(--pad-deep)"/>
        </linearGradient>
      </defs>
      <rect width="620" height="354" fill="url(#sunset-scene)"/>
    </svg>
    <div class="back-band">
      <h2 class="back-company">Summit BladeAir</h2>
      <p class="back-services">Airport · Tour guide · Heliport</p>
    </div>
  </section>
</div>
</body>
</html>
```